New Business Card Design Project

We require a business card design for Vexalund, a newly established Indian company.
Our focus is on the development, manufacturing, and export of a diverse array of pharmaceutical products on a global scale. The card should convey a professional appearance, as our primary markets are in Africa, China, and Southeast Asian nations.
We envision a two-sided business card, with the reverse side dedicated to a logo set against a solid color or an elegantly designed pattern. The corners should be rounded. We would appreciate seeing both horizontal and vertical design options. We trust the designer to utilize their expertise in creating this design.

The content for the business card is included in the attached Word file.

Target Market(s)

Our primary markets are in Africa, China, and Southeast Asian, Latin America, Maldives, Sri Lanka

Industry/Entity Type

Pharmaceutical Manufacturing and Export

Contact Information for Business Card

Colors

Designer to choose colors to be used in the design.

Requirements
Must have
• The reverse side of the business card features solely the logo along with the tagline, "Wellness for All."
Should not have
• The logo should not exceed two instances, encompassing both the front and back sides of the card.

```html
<!DOCTYPE html>
<html lang="en">
<head>
<meta charset="utf-8">
<title>Vexalund Business Card</title>
<link rel="stylesheet" href="https://fonts.googleapis.com/css2?family=Montserrat:wght@400;500;700;800&display=swap">
<style>
  :root {
    --canvas: #ecebe8;
    --brand-blue: #29a3dd;
    --brand-blue-deep: #1d8cc4;
    --brand-coral: #ee5b4a;
    --ink: #222222;
    --white: #ffffff;
  }
  * { box-sizing: border-box; margin: 0; padding: 0; }
  html, body { width: 1200px; height: 931px; overflow: hidden; }
  body {
    background: var(--canvas);
    font-family: "Montserrat", Arial, sans-serif;
    position: relative;
  }
  .card {
    position: absolute;
    width: 680px;
    height: 388px;
    border-radius: 26px;
    overflow: hidden;
    box-shadow: 0 10px 28px rgba(0,0,0,0.22);
  }
  /* Reverse side */
  .card-back {
    left: 60px; top: 60px;
    background: var(--brand-blue);
  }
  .back-pattern {
    position: absolute; inset: 0;
    background: linear-gradient(115deg, #6cc3ee 0%, var(--brand-blue) 40%, var(--brand-blue-deep) 100%);
  }
  .back-divider {
    position: absolute; left: 0; right: 0; top: 200px;
    height: 1px; background: rgba(255,255,255,0.25);
  }
  .back-brand {
    position: absolute; right: 46px; top: 150px;
    display: flex; align-items: center; gap: 10px;
    color: var(--white); font-weight: 700; font-size: 26px;
  }
  .back-brand .dot {
    width: 14px; height: 14px; border-radius: 50%; background: var(--brand-coral);
  }
  .tagline {
    position: absolute; left: 0; right: 0; top: 250px;
    text-align: center; color: var(--white);
    font-weight: 700; font-size: 20px; letter-spacing: 0.5px;
  }
  /* Front side */
  .card-front {
    left: 460px; top: 483px;
    background: var(--white);
  }
  .front-decor {
    position: absolute; right: 0; top: 0;
    width: 300px; height: 100%;
    background: linear-gradient(135deg, rgba(238,91,74,0.85) 0%, rgba(238,91,74,0.55) 35%, rgba(41,163,221,0.75) 65%, rgba(41,163,221,0.9) 100%);
  }
  .front-info {
    position: absolute; left: 40px; top: 36px;
    color: var(--ink);
  }
  .brand-name {
    color: var(--brand-blue);
    font-weight: 800; font-size: 60px; line-height: 1;
    letter-spacing: -0.5px;
  }
  .person-name {
    margin-top: 26px;
    color: var(--brand-blue);
    font-weight: 700; font-size: 28px; line-height: 1;
  }
  .person-role {
    margin-top: 8px; font-size: 17px; font-weight: 400;
  }
  .address {
    margin-top: 22px; font-size: 16px; line-height: 1.35; font-weight: 400;
  }
  .contacts {
    list-style: none; margin-top: 18px;
    font-size: 16px; line-height: 1; font-weight: 400;
  }
  .contacts li {
    display: flex; align-items: center; gap: 10px; margin-bottom: 10px;
  }
  .contacts svg { width: 16px; height: 16px; fill: var(--brand-blue); flex: none; }
</style>
</head>
<body>

  <section class="card card-back" aria-label="Card reverse side">
    <div class="back-pattern" role="img" aria-label="Repeating brand pattern in shades of blue"></div>
    <div class="back-divider"></div>
    <div class="back-brand"><span class="dot"></span>Vexalund</div>
    <p class="tagline">Wellness for All</p>
  </section>

  <section class="card card-front" aria-label="Card front side">
    <div class="front-decor" role="img" aria-label="Large brand decoration in blue and coral"></div>
    <div class="front-info">
      <h1 class="brand-name">Vexalund</h1>
      <h2 class="person-name">Rohan K. Sarvade</h2>
      <p class="person-role">CEO</p>
      <p class="address">14, Nandan Colony,<br>Akola, 444001, India</p>
      <ul class="contacts">
        <li>
          <svg viewBox="0 0 16 16" aria-hidden="true"><path d="M3.5 1.5l2.5 0 1 3.5-1.7 1.2c.8 1.8 2.2 3.2 4 4l1.2-1.7 3.5 1v2.5c0 .8-.7 1.5-1.5 1.5C6.6 13.5 2.5 9.4 2 3c0-.8.7-1.5 1.5-1.5z"/></svg>
          +919876501234
        </li>
        <li>
          <svg viewBox="0 0 16 16" aria-hidden="true"><path d="M1 3.5h14v9H1z" opacity=".9"/><path d="M1 3.5l7 5 7-5" fill="none" stroke="#fff" stroke-width="1.3"/></svg>
          sarvade@vexalund.com
        </li>
        <li>
          <svg viewBox="0 0 16 16" aria-hidden="true"><circle cx="8" cy="8" r="7"/><path d="M1 8h14M8 1c2.5 2.5 2.5 11.5 0 14M8 1c-2.5 2.5-2.5 11.5 0 14" fill="none" stroke="#fff" stroke-width="1"/></svg>
          www.vexalund.com
        </li>
      </ul>
    </div>
  </section>

</body>
</html>
```